Investment Memorandum Document

IM for Harbourline Lending Fund - is the document that needs work

Make sure it is all done in MS WORD so that i or lawyers can edit some words if required

the IM is NOT final but its 95% of the way there. Maybe a few more pages and wording changes - but that is something i can do i guess or you can easier adjust

Just to typeset and pretty it all up - a few sample finished products have been uploaded for reference.

KTR IM is the one i like - but feel free to show off your skills

put 1.2 to 1.8 all in contrasting row tables

Target Market(s)

Individual and Institutional investors with money

Industry/Entity Type

Investment Banking

Colors

Designer to choose colors to be used in the design.

Requirements
Must have
• clear professional layout and easy on the eye
• https://www.filevaultexample.net/sh/84k3p77zrm2wqtn/BBDfpqWem3PvtsLxQZMUD41Lb?dl=0
• use the link above for high res images
Nice to have
• pictures and graphics
Should not have
• cartoons

```html
<!DOCTYPE html>
<html lang="en">
<head>
<meta charset="utf-8">
<title>Harbourline Diversified Commercial Income Fund – Information Memorandum</title>
<link href="https://fonts.googleapis.com/css2?family=Arimo:ital,wght@0,400;0,700;1,400&display=swap" rel="stylesheet">
<style>
  :root {
    --canvas: #e9e9e7;
    --paper: #ffffff;
    --ink: #3a3a3a;
    --heading: #2a9fd6;
    --footer-ink: #666666;
    --tab-gold: #b8862e;
    --tab-blue: #5a8db3;
    --spine: #d9d9d9;
  }
  * { box-sizing: border-box; margin: 0; padding: 0; }
  html, body { width: 1200px; height: 1200px; overflow: hidden; }
  body {
    background: var(--canvas);
    font-family: "Arimo", Arial, sans-serif;
    color: var(--ink);
    position: relative;
  }
  .spread {
    position: absolute;
    left: 200px;
    width: 800px;
    height: 566px;
    display: flex;
    background: var(--paper);
    box-shadow: 0 2px 10px rgba(0,0,0,0.12);
  }
  .spread--gold { top: 20px; --tab: var(--tab-gold); }
  .spread--blue { top: 614px; --tab: var(--tab-blue); }
  .page {
    position: relative;
    width: 400px;
    height: 566px;
    padding: 46px 36px 0 40px;
  }
  .page--left { border-right: 1px solid var(--spine); padding-left: 44px; padding-right: 32px; }
  .page--right { padding-left: 40px; padding-right: 38px; padding-top: 44px; }
  .section-title {
    font-size: 5.6px;
    font-weight: 700;
    color: var(--heading);
    letter-spacing: 0.15px;
    text-transform: uppercase;
    margin: 5px 0 3.5px;
    padding-bottom: 1.6px;
    position: relative;
  }
  .section-title::after {
    content: "";
    position: absolute;
    left: 0; bottom: 0;
    width: 18px; height: 0.8px;
    background: var(--heading);
  }
  .section-title:first-child { margin-top: 0; }
  .body-text {
    font-size: 5.6px;
    line-height: 7.2px;
    text-align: justify;
    margin-bottom: 4px;
  }
  .body-text b { font-weight: 700; }
  .page-footer {
    position: absolute;
    left: 0; right: 0;
    bottom: 24px;
    height: 12px;
    display: flex;
    align-items: center;
  }
  .footer-title {
    font-size: 5.4px;
    font-style: italic;
    color: var(--footer-ink);
    flex: 1;
  }
  .page--left .footer-title { padding-left: 48px; }
  .page--right .footer-title { padding-left: 44px; }
  .footer-mark {
    width: 8px; height: 8px;
    background: var(--tab);
    margin-right: 5px;
  }
  .page-tab {
    width: 50px; height: 12px;
    background: var(--tab);
    color: #ffffff;
    font-size: 5.4px;
    line-height: 12px;
    padding-left: 10px;
  }
</style>
</head>
<body>

<section class="spread spread--gold">
  <article class="page page--left">
    <h2 class="section-title">Notice</h2>
    <p class="body-text">This Information Memorandum is dated XXX and is issued by Meridian Trust and Lending Corporation Pty Ltd ACN 149 000 218, holder of AFS licence number 400100 (<b>Trustee</b>), which is the trustee of the Harbourline Diversified Commercial Income Fund (<b>Fund</b>).</p>
    <p class="body-text">The purpose of this IM is to provide information for prospective investors to decide whether they wish to invest in the Fund.</p>
    <p class="body-text">The Trustee has appointed Harbourline Asset Management Pty Ltd (<b>Investment Manager</b>) as the investment manager of the Fund under the Investment Management Agreement. The Investment Manager is an authorised representative (number 1200000) of Meridian Trust and Lending Corporation Pty Ltd.</p>
    <p class="body-text">The Fund's trust deed (<b>Trust Deed</b>) provides for different Classes of Units. Under the Trust Deed, the different Classes of Units may have different rights and obligations. The performance of different Classes of Units may also differ depending on the investments of that Class. Holders of different Classes of Units will be treated fairly.</p>
    <h2 class="section-title">No Disclosure Required</h2>
    <p class="body-text">This IM is intended to provide potential Investors with information only and does not constitute a product disclosure statement or other disclosure document required by the <i>Corporations Act 2001</i> (Cth) (<b>Act</b>). This IM has not been lodged with the Australian Securities and Investments Commission (<b>ASIC</b>) or any other government body.</p>
    <p class="body-text">The offer made under this IM is only available to persons who qualify as wholesale clients (as defined in section 761G (7) of the Act) or sophisticated investors (as defined in section 761GA of the Act) (collectively, <b>Qualified Investors</b>). The Trustee will not issue Units in the Fund to a person unless it is satisfied that the person is a Qualified Investor.</p>
    <h2 class="section-title">Restrictions on Distribution</h2>
    <p class="body-text">This IM does not constitute, and may not be used for the purposes of, an offer of Units or an invitation to apply to participate in the Fund by any person in any jurisdiction in which such offer or invitation is not authorised or to any person to whom it is unlawful to make such an offer or invitation.</p>
    <p class="body-text">No action has been taken to register or qualify interests in the Fund, the invitation to participate in the Fund, or to otherwise permit any public offering of Fund interests in any jurisdiction other than Australia. It is the responsibility of prospective Investors to satisfy themselves as to full compliance with the relevant laws and regulations of any jurisdiction in connection with any application to participate in the Fund.</p>
    <p class="body-text">By receiving and viewing this IM, the recipient is warranting that they are legally entitled to do so and that the securities laws of their relevant jurisdiction do not prohibit them from acquiring interests in the Fund.</p>
    <p class="body-text">In particular, this product has not been and will not be registered under the US Securities Act or the securities laws of any state of the United States and may not be offered, sold, delivered or transferred in the United States or to, or for the account of, any "US Person". Neither this IM, Application Form or other material relating to this product may be distributed in the United States.</p>
    <p class="body-text">With respect to Australian jurisdiction, this IM has been prepared on the basis that the prospective Investors are wholesale clients or sophisticated investors, not retail clients within the meaning of the Corporations Act.</p>
    <p class="body-text">Accordingly, this IM is not a product disclosure statement and does not contain all of the information that would be included in a product disclosure statement issued under the Corporations Act.</p>
    <p class="body-text">The Trustee may in the future take actions to offer interests in the Fund in other jurisdictions.</p>
    <h2 class="section-title">No Responsibility for Contents of Document</h2>
    <p class="body-text">To the maximum extent permitted by law, none of the Trustee, the Investment Manager, or any of their associates, related parties, directors, officers, employees, advisors or representatives make any recommendation in relation to the Fund, or make any representation or warranty, express or implied, as to the accuracy, reliability or completeness of the information contained in this IM.</p>
    <p class="body-text">This IM does not purport to contain all the information that a prospective Investor may require in evaluating a possible investment in the Fund.</p>
    <p class="body-text">This IM must be read in conjunction with the Fund's Trust Deed which is available (free of charge) by contacting the Trustee on +61 3 9000 4417. To the extent there are any inconsistencies between the Trust Deed and this IM, the Trust Deed will prevail.</p>
    <footer class="page-footer">
      <span class="footer-title">Harbourline Diversified Commercial Income Fund – Information Memorandum</span>
      <span class="footer-mark"></span>
      <span class="page-tab">3</span>
    </footer>
  </article>
  <article class="page page--right">
    <h2 class="section-title">No Distribution</h2>
    <p class="body-text">Distribution of this IM to any person other than the persons receiving a copy of this IM from the Trustee or the Investment Manager is unauthorised. Any photocopying, disclosure or alteration of the contents of this IM, and any forwarding of this IM, or any portion thereof by electronic mail or any other means to any person other than the person receiving this IM from the Trustee or Investment Manager is prohibited.</p>
    <h2 class="section-title">Not Regulated by APRA</h2>
    <p class="body-text">The Trustee is not authorised under the <i>Banking Act 1959</i> (Cth) and is not supervised by APRA, and investments in the Fund are not covered by the deposit or protection provisions available to depositors that make a deposit with an Australian ADI.</p>
    <h2 class="section-title">Forward-Looking Statements</h2>
    <p class="body-text">This IM includes forward looking statements that may contain words such as "believe", "intend", "estimate", "expect" and words of similar meaning. All statements other than statements of historical facts included in this IM, including, without limitation, those regarding an investee's financial position and business or investment strategy, plans and objectives are forward looking statements. Such forward looking statements involve known and unknown risks, uncertainties and other important factors that could cause the actual results, performance or achievements of an investee or associated project to be materially different from future results, performance or achievements expressed or implied by such forward looking statements.</p>
    <p class="body-text">Any forward looking statements are based on numerous assumptions regarding a Project, the present and future business, the investment strategies and the markets in which a Project will operate in the future. These forward-looking statements are current only as at the date of this IM. Accordingly, there can be no assurance that such statements, estimates or projections will be realised.</p>
    <h2 class="section-title">Independent Advice Recommended</h2>
    <p class="body-text">Prospective Investors should not construe the contents of this IM as tax, legal or investment advice. The information contained in this IM is general information only and does not take into account your objectives, financial situations or needs. An investment in the Fund should be regarded as speculative and may not be appropriate for all persons or entities. You should seek appropriate professional advice and should conduct your own independent investigation and analysis regarding any information contained in this IM before making any decision to invest in the Fund. You should rely on your own enquiries, in particular in obtaining your own legal, investment and tax advice in determining whether to invest in the Fund.</p>
    <h2 class="section-title">No Guarantee</h2>
    <p class="body-text">An investment in the Fund is subject to investment risk, including the loss of income and capital invested. None of the Trustee, the Investment Manager or any of their directors, officers, employees, advisers or representatives guarantee the rate of return or performance of the Fund, the meeting of the objectives of the Fund, nor do they guarantee repayment of the amount invested in the Fund.</p>
    <h2 class="section-title">Trustee Limitation of Liability</h2>
    <p class="body-text">Except in certain circumstances (including fraud, negligence or default by the Trustee), the Trustee enters into transactions for the Fund in its capacity as trustee of the Fund only, not in its own capacity, and its liabilities in relation to those transactions is limited to the assets of the Fund.</p>
    <h2 class="section-title">Updated Information</h2>
    <p class="body-text">The information contained in this IM may change and the IM may be updated or replaced from time to time. Unless the changed information is materially adverse to you, the Trustee may not always update or replace this IM to reflect the changed information. Updated information can be obtained by contacting the Trustee on +61 3 9000 4417.</p>
    <h2 class="section-title">Confidentiality</h2>
    <p class="body-text">This IM is confidential and is provided to prospective Investors for them to consider investing in the Fund. Its use for any other purposes is not permitted. It may not be reproduced or redistributed, in whole or in part, and its contents may not be disclosed to any person.</p>
    <h2 class="section-title">Glossary</h2>
    <p class="body-text">Certain capitalised words and expressions used in this IM are defined in the Glossary. All references to dollar amounts in this IM are to Australian Dollars (<b>AUD</b>), unless otherwise stated.</p>
    <footer class="page-footer">
      <span class="footer-title">Harbourline Diversified Commercial Income Fund – Information Memorandum</span>
      <span class="footer-mark"></span>
      <span class="page-tab">4</span>
    </footer>
  </article>
</section>

<section class="spread spread--blue">
  <article class="page page--left">
    <h2 class="section-title">Notice</h2>
    <p class="body-text">This Information Memorandum is dated XXX and is issued by Meridian Trust and Lending Corporation Pty Ltd ACN 149 000 218, holder of AFS licence number 400100 (<b>Trustee</b>), which is the trustee of the Harbourline Diversified Commercial Income Fund (<b>Fund</b>).</p>
    <p class="body-text">The purpose of this IM is to provide information for prospective investors to decide whether they wish to invest in the Fund.</p>
    <p class="body-text">The Trustee has appointed Harbourline Asset Management Pty Ltd (<b>Investment Manager</b>) as the investment manager of the Fund under the Investment Management Agreement. The Investment Manager is an authorised representative (number 1200000) of Meridian Trust and Lending Corporation Pty Ltd.</p>
    <p class="body-text">The Fund's trust deed (<b>Trust Deed</b>) provides for different Classes of Units. Under the Trust Deed, the different Classes of Units may have different rights and obligations. The performance of different Classes of Units may also differ depending on the investments of that Class. Holders of different Classes of Units will be treated fairly.</p>
    <h2 class="section-title">No Disclosure Required</h2>
    <p class="body-text">This IM is intended to provide potential Investors with information only and does not constitute a product disclosure statement or other disclosure document required by the <i>Corporations Act 2001</i> (Cth) (<b>Act</b>). This IM has not been lodged with the Australian Securities and Investments Commission (<b>ASIC</b>) or any other government body.</p>
    <p class="body-text">The offer made under this IM is only available to persons who qualify as wholesale clients (as defined in section 761G (7) of the Act) or sophisticated investors (as defined in section 761GA of the Act) (collectively, <b>Qualified Investors</b>). The Trustee will not issue Units in the Fund to a person unless it is satisfied that the person is a Qualified Investor.</p>
    <h2 class="section-title">Restrictions on Distribution</h2>
    <p class="body-text">This IM does not constitute, and may not be used for the purposes of, an offer of Units or an invitation to apply to participate in the Fund by any person in any jurisdiction in which such offer or invitation is not authorised or to any person to whom it is unlawful to make such an offer or invitation.</p>
    <p class="body-text">No action has been taken to register or qualify interests in the Fund, the invitation to participate in the Fund, or to otherwise permit any public offering of Fund interests in any jurisdiction other than Australia. It is the responsibility of prospective Investors to satisfy themselves as to full compliance with the relevant laws and regulations of any jurisdiction in connection with any application to participate in the Fund.</p>
    <p class="body-text">By receiving and viewing this IM, the recipient is warranting that they are legally entitled to do so and that the securities laws of their relevant jurisdiction do not prohibit them from acquiring interests in the Fund.</p>
    <p class="body-text">In particular, this product has not been and will not be registered under the US Securities Act or the securities laws of any state of the United States and may not be offered, sold, delivered or transferred in the United States or to, or for the account of, any "US Person". Neither this IM, Application Form or other material relating to this product may be distributed in the United States.</p>
    <p class="body-text">With respect to Australian jurisdiction, this IM has been prepared on the basis that the prospective Investors are wholesale clients or sophisticated investors, not retail clients within the meaning of the Corporations Act.</p>
    <p class="body-text">Accordingly, this IM is not a product disclosure statement and does not contain all of the information that would be included in a product disclosure statement issued under the Corporations Act.</p>
    <p class="body-text">The Trustee may in the future take actions to offer interests in the Fund in other jurisdictions.</p>
    <h2 class="section-title">No Responsibility for Contents of Document</h2>
    <p class="body-text">To the maximum extent permitted by law, none of the Trustee, the Investment Manager, or any of their associates, related parties, directors, officers, employees, advisors or representatives make any recommendation in relation to the Fund, or make any representation or warranty, express or implied, as to the accuracy, reliability or completeness of the information contained in this IM.</p>
    <p class="body-text">This IM does not purport to contain all the information that a prospective Investor may require in evaluating a possible investment in the Fund.</p>
    <p class="body-text">This IM must be read in conjunction with the Fund's Trust Deed which is available (free of charge) by contacting the Trustee on +61 3 9000 4417. To the extent there are any inconsistencies between the Trust Deed and this IM, the Trust Deed will prevail.</p>
    <footer class="page-footer">
      <span class="footer-title">Harbourline Diversified Commercial Income Fund – Information Memorandum</span>
      <span class="footer-mark"></span>
      <span class="page-tab">3</span>
    </footer>
  </article>
  <article class="page page--right">
    <h2 class="section-title">No Distribution</h2>
    <p class="body-text">Distribution of this IM to any person other than the persons receiving a copy of this IM from the Trustee or the Investment Manager is unauthorised. Any photocopying, disclosure or alteration of the contents of this IM, and any forwarding of this IM, or any portion thereof by electronic mail or any other means to any person other than the person receiving this IM from the Trustee or Investment Manager is prohibited.</p>
    <h2 class="section-title">Not Regulated by APRA</h2>
    <p class="body-text">The Trustee is not authorised under the <i>Banking Act 1959</i> (Cth) and is not supervised by APRA, and investments in the Fund are not covered by the deposit or protection provisions available to depositors that make a deposit with an Australian ADI.</p>
    <h2 class="section-title">Forward-Looking Statements</h2>
    <p class="body-text">This IM includes forward looking statements that may contain words such as "believe", "intend", "estimate", "expect" and words of similar meaning. All statements other than statements of historical facts included in this IM, including, without limitation, those regarding an investee's financial position and business or investment strategy, plans and objectives are forward looking statements. Such forward looking statements involve known and unknown risks, uncertainties and other important factors that could cause the actual results, performance or achievements of an investee or associated project to be materially different from future results, performance or achievements expressed or implied by such forward looking statements.</p>
    <p class="body-text">Any forward looking statements are based on numerous assumptions regarding a Project, the present and future business, the investment strategies and the markets in which a Project will operate in the future. These forward-looking statements are current only as at the date of this IM. Accordingly, there can be no assurance that such statements, estimates or projections will be realised.</p>
    <h2 class="section-title">Independent Advice Recommended</h2>
    <p class="body-text">Prospective Investors should not construe the contents of this IM as tax, legal or investment advice. The information contained in this IM is general information only and does not take into account your objectives, financial situations or needs. An investment in the Fund should be regarded as speculative and may not be appropriate for all persons or entities. You should seek appropriate professional advice and should conduct your own independent investigation and analysis regarding any information contained in this IM before making any decision to invest in the Fund. You should rely on your own enquiries, in particular in obtaining your own legal, investment and tax advice in determining whether to invest in the Fund.</p>
    <h2 class="section-title">No Guarantee</h2>
    <p class="body-text">An investment in the Fund is subject to investment risk, including the loss of income and capital invested. None of the Trustee, the Investment Manager or any of their directors, officers, employees, advisers or representatives guarantee the rate of return or performance of the Fund, the meeting of the objectives of the Fund, nor do they guarantee repayment of the amount invested in the Fund.</p>
    <h2 class="section-title">Trustee Limitation of Liability</h2>
    <p class="body-text">Except in certain circumstances (including fraud, negligence or default by the Trustee), the Trustee enters into transactions for the Fund in its capacity as trustee of the Fund only, not in its own capacity, and its liabilities in relation to those transactions is limited to the assets of the Fund.</p>
    <h2 class="section-title">Updated Information</h2>
    <p class="body-text">The information contained in this IM may change and the IM may be updated or replaced from time to time. Unless the changed information is materially adverse to you, the Trustee may not always update or replace this IM to reflect the changed information. Updated information can be obtained by contacting the Trustee on +61 3 9000 4417.</p>
    <h2 class="section-title">Confidentiality</h2>
    <p class="body-text">This IM is confidential and is provided to prospective Investors for them to consider investing in the Fund. Its use for any other purposes is not permitted. It may not be reproduced or redistributed, in whole or in part, and its contents may not be disclosed to any person.</p>
    <h2 class="section-title">Glossary</h2>
    <p class="body-text">Certain capitalised words and expressions used in this IM are defined in the Glossary. All references to dollar amounts in this IM are to Australian Dollars (<b>AUD</b>), unless otherwise stated.</p>
    <footer class="page-footer">
      <span class="footer-title">Harbourline Diversified Commercial Income Fund – Information Memorandum</span>
      <span class="footer-mark"></span>
      <span class="page-tab">4</span>
    </footer>
  </article>
</section>

</body>
</html>
```